Accountant website

Please design a accountant website for www.fenwaybridgeadvisory.com.au. This site is majorly out of date, and is not supported by modern browsers.

The style should use the reds from the design at dev.fenwaybridgeadvisory.com.au, and should be modern and make use of Slides (large content slides that the user scrolls through on the front page).

The content is largely already on the site, however happy to move some around to suit the modern design as required.

The dev.fenwaybridgeadvisory.com.au was a rough mock up that I have completed that the client is "happy" with the direction, however this needs a lot of polish and finishing touches, and I will accept designs that differ from this, but highly recommend that this is used as a guide.

Ready to be sliced PSD Only - HTML no required.

In all honesty, although I can technically do a lot of this, the polished finished I want for this site has eluded me in a few attempts, and therefore I am looking out there at you much more artistic people to finish (or redesign if required) this site.

Target Market(s)

Higher end Small - Medium Business

Industry/Entity Type

Accountant

Requirements
Must have
• Must use the logo from dev.fenwaybridgeadvisory.com.au use exactly the red colours as defined in this layout. A basic layout PSD (to get the colour etc) and the logo in ai format is attached to this project. Please ignore the SSL warning on the development site.

The final product does NOT have to be the same as shown on dev.fenwaybridgeadvisory.com.au however the red colour scheme must be used. The client DOES want the logo on the RIGHT.

Must have a front landing page design, and a page layout that considers the other page content (at least one separate PSD)
Nice to have
• I really am looking at a slide format for the front page simular to:

http://www.quillo.com/au/
http://www.vaultmoor.com/

The attached photos should be used on the site. Was considering a rotating banner with these images are a watermark background on a solid Red header bar, but happy to be shown other options.
Should not have
• Please no "Layout Goblin" submissions.

```html
<!DOCTYPE html>
<html lang="en">
<head>
<meta charset="utf-8">
<title>Fenway Bridge Advisory</title>
<link rel="stylesheet" href="https://fonts.googleapis.com/css2?family=Source+Sans+3:wght@300;400;600&family=Oswald:wght@500&display=swap">
<style>
:root{
  --red:#a32f30;
  --red-text:#b0272a;
  --ink:#3d3d3d;
  --body:#6a6a6a;
  --white:#ffffff;
  --soft:#ececec;
  --footer:#3a3a3a;
  --footer-deep:#2a2a2a;
  --footer-text:#d8d8d8;
}
*{margin:0;padding:0;box-sizing:border-box}
html,body{width:750px;height:1200px;overflow:hidden;background:var(--white)}
body{font-family:"Source Sans 3",sans-serif;color:var(--ink)}
.page{position:relative;width:750px;height:1200px;overflow:hidden}
.abs{position:absolute}

/* header */
.site-header{left:0;top:0;width:750px;height:86px;background:var(--white)}
.brand{right:54px;top:26px;font-size:19px;font-weight:600;color:var(--ink);line-height:19px;letter-spacing:.5px;text-transform:uppercase;text-align:right}
.client-login{left:54px;top:18px;font-size:12px;color:var(--red-text);letter-spacing:.3px}
.main-nav{left:54px;top:55px;display:flex;gap:23px;font-size:12px;color:var(--ink);letter-spacing:.2px}
.main-nav .active{color:var(--red-text)}

/* hero */
.hero{left:0;top:86px;width:750px;height:315px;background:linear-gradient(100deg,#c6cfd8 0%,#a9b6c2 40%,#d7d4cf 65%,#8f9a86 100%)}
.hero-caption{left:55px;top:213px;width:285px;height:84px;background:rgba(40,40,40,.72);padding:11px 13px;color:var(--white)}
.hero-caption h1{font-family:"Oswald",sans-serif;font-weight:500;font-size:18px;letter-spacing:0;line-height:22px;margin-bottom:7px;white-space:nowrap}
.hero-caption p{font-size:9.5px;line-height:15px}
.slider-dots{right:54px;top:301px;display:flex;gap:3px}
.slider-dots span{width:6px;height:6px;border-radius:50%;background:#333;border:1px solid #fff}
.slider-dots span:first-child{background:#fff}

/* intro band */
.intro{left:0;top:401px;width:750px;height:268px;background:var(--red);color:var(--white);text-align:center}
.intro h2{position:absolute;left:0;width:750px;top:22px;font-size:18px;font-weight:600}
.intro .lead{position:absolute;left:54px;width:642px;top:55px;font-size:8px;line-height:14px}
.service{position:absolute;top:108px;width:190px;text-align:center}
.service svg{display:block;margin:0 auto 6px;height:58px}
.service h3{font-size:13px;font-weight:600;margin-bottom:4px}
.service p{font-size:8.5px;line-height:13.5px;letter-spacing:.3px;width:156px;margin:0 auto}

/* welcome */
.welcome{left:84px;top:694px;width:408px}
.welcome h2{font-size:18px;font-weight:300;color:var(--ink)}
.welcome h2 span{color:var(--red-text)}
.welcome h4,.difference h4{font-size:11.5px;font-weight:400;margin:6px 0 8px}
.welcome p,.difference p{font-size:7.8px;line-height:13.5px;color:var(--body)}
.testimonials{left:519px;top:697px}
.testimonials h3{font-size:14px;font-weight:300;margin-bottom:9px}
.client-grid{display:grid;grid-template-columns:repeat(3,48px);gap:4px;row-gap:7px}
.client-grid div{width:48px;height:45px;background:linear-gradient(160deg,#c9a88e,#7a5e4c)}

/* difference */
.difference-band{left:0;top:852px;width:750px;height:194px;background:var(--soft)}
.advisor-photo{left:98px;top:860px;width:124px;height:186px;background:linear-gradient(180deg,#d9cfc6 0%,#9a9894 50%,#858585 100%);border-radius:60px 60px 0 0}
.difference{left:266px;top:876px;width:406px}
.difference h2{font-size:18px;font-weight:300;color:var(--red-text)}

/* footer */
.site-footer{left:0;top:1046px;width:750px;height:117px;background:var(--footer)}
.footer-col{position:absolute;top:16px;color:var(--footer-text)}
.footer-col h5{font-size:11.5px;font-weight:400;color:var(--white);margin-bottom:5px}
.footer-col li{list-style:none;font-size:8.2px;line-height:18px}
.badge{position:absolute;left:600px;top:41px;width:96px;height:41px;background:#8c8c8c;border:1px solid #a6a6a6}
.bottom-bar{left:0;top:1163px;width:750px;height:37px;background:var(--footer-deep);color:var(--footer-text)}
.copyright{position:absolute;left:54px;top:13px;font-size:8px}
.social{position:absolute;right:54px;top:9px;display:flex;gap:12px}
.social span{width:18px;height:18px;border-radius:50%;background:#5f6e7e}
</style>
</head>
<body>
<div class="page">

  <header class="site-header abs">
    <div class="client-login abs">CLIENT LOGIN</div>
    <nav class="main-nav abs">
      <span class="active">HOME</span><span>ABOUT</span><span>SERVICES</span><span>CONTACT</span><span>TESTIMONIALS</span><span>NEWS</span>
    </nav>
    <div class="brand abs">Fenway Bridge<br>Advisory</div>
  </header>

  <section class="hero abs" role="img" aria-label="Photo of a smiling woman in a red dress at a marina with moored yachts">
    <div class="hero-caption abs">
      <h1>THE DAYS OF BUYING EXPENSIVE</h1>
      <p>Jerta baditaut onsequser untur magni dolores eoquie volup tate msequi nesciunt. Voluptatem accusantium dolorem.</p>
    </div>
    <div class="slider-dots abs"><span></span><span></span><span></span><span></span></div>
  </section>

  <section class="intro abs">
    <h2>Getting to Know Fenway Bridge Advisory</h2>
    <p class="lead">Vivamus sagittis lacus vel augue laoreet rutrum faucibus dolor auctor. Aenean lacinia bibendum nulla sed consectetur. Because we think it's time for a new exciting challeng e! Are you ready for an adventure to remember for a lifetime? Accusantium quam, ultricies eget tempor id, aliquam eget nibh et. Maecen aliquam, risus at sempe</p>

    <div class="service" style="left:83px">
      <svg viewBox="0 0 60 58" fill="none" stroke="#fff" stroke-width="3">
        <path d="M10 2h24l12 12v40H10z"/><path d="M34 2v12h12"/>
        <path d="M16 22h20M16 30h16M16 38h12M16 46h10"/>
        <circle cx="46" cy="42" r="11" fill="#a32f30"/><path d="M46 38v10M46 34v1"/>
      </svg>
      <h3>Business Establishment</h3>
      <p>Lorem ipsum dolor sit amet adipis msan. Morbi ut elit utipsum tristiquea Pellentesque habitant morbi.</p>
    </div>
    <div class="service" style="left:280px">
      <svg viewBox="0 0 60 58" fill="none" stroke="#fff" stroke-width="3" stroke-linejoin="round">
        <path d="M4 36L54 4 44 54 30 40z"/><path d="M54 4L24 44l6-4"/><path d="M24 44v10l6-14"/>
      </svg>
      <h3>Business Cessation</h3>
      <p>Lorem ipsum dolor sit amet adipis msan. Morbi ut elit utipsum tristiquea Pellentesque habitant morbi.</p>
    </div>
    <div class="service" style="left:476px">
      <svg viewBox="0 0 60 58" fill="#fff">
        <path d="M30 2a16 16 0 0 0-10 28c2 2 3 5 3 8h14c0-3 1-6 3-8A16 16 0 0 0 30 2z"/>
        <rect x="22" y="41" width="16" height="3"/><rect x="22" y="46" width="16" height="3"/><rect x="25" y="51" width="10" height="4" rx="2"/>
      </svg>
      <h3>Business Services</h3>
      <p>Lorem ipsum dolor sit amet adipis msan. Morbi ut elit utipsum tristiquea Pellentesque habitant morbi.</p>
    </div>
  </section>

  <section class="welcome abs">
    <h2>Welcome to <span>Fenway</span></h2>
    <h4>Doloremque laudantium totames</h4>
    <p>Pellentesque habitant morbi tristique senectus et netus et malesuada fames ac turpis egestas. Lorem ipiisum dolor sit amet, consectetur adipiscing elit. Nunc id lobortis diam, vel lobortis ipsum.At vero eos et accusamiu s et iusto odio dignissimos ducimus qui blanditiis praesentium voluptatu deleniti atque corrupti quos dolore s et quas molestias excep turi sint occaecati cupiditate non provident similique Lorem ipsum dolor sit amet, c onsectetur adipisicing elitsed dore eiusmod tempor incididunt ut labore etman dolore magna aliqua nimad minim veniam pulsar adiya</p>
  </section>

  <aside class="testimonials abs">
    <h3>View wht our client says</h3>
    <div class="client-grid">
      <div role="img" aria-label="Client portrait"></div>
      <div role="img" aria-label="Client portrait"></div>
      <div role="img" aria-label="Client portrait"></div>
      <div role="img" aria-label="Client portrait"></div>
      <div role="img" aria-label="Client portrait"></div>
      <div role="img" aria-label="Client portrait"></div>
    </div>
  </aside>

  <section class="difference-band abs"></section>
  <div class="advisor-photo abs" role="img" aria-label="Photo of a businesswoman in a grey suit with arms folded"></div>
  <section class="difference abs">
    <h2>Fenway Bridge Advisory Difference</h2>
    <h4>Doloremque laudantium totames</h4>
    <p>Pellentesque habitant morbi tristique senectus et netus et malesuada fames ac turpis egestas. Lorem ipiisum dolor sit amet, consectetur adipiscing elit. Nunc id lobortis diam, vel lobortis ipsum.At vero eos et accusamiu s et iusto odio dignissimos ducimus qui blanditiis praesentium voluptatu deleniti atque corrupti quos dolore s et quas molestias excep turi sint occaecati cupiditate non provident similique Lorem ipsum dolor sit amet, c onsectetur adipisicing elitsed dore eiusmod tempor incididunt ut labore etman dolore magna aliqua nimad minim veniam pulsar adiya</p>
  </section>

  <footer class="site-footer abs">
    <div class="footer-col" style="left:54px"><h5>US States</h5><ul><li>Team Portal</li><li>FeedbacK Exchange</li><li>Proin sit amet nulla</li><li>Consectetur adipiscing</li></ul></div>
    <div class="footer-col" style="left:193px"><h5>Who We Are</h5><ul><li>PressLeaf</li><li>Searchly</li><li>Vidstream</li><li>Lensbury</li></ul></div>
    <div class="footer-col" style="left:313px"><h5>Outreach</h5><ul><li>Web Design Tauranga</li><li>Web Design Papamoa</li><li>Web Design Te Puke</li><li>Web Design Mt Maunganui</li></ul></div>
    <div class="footer-col" style="left:463px"><h5>Business Consulting</h5><ul><li>Web Design Tauranga</li><li>Web Design Papamoa</li><li>Web Design Te Puke</li><li>Web Design Mt Maunganui</li></ul></div>
    <div class="badge" role="img" aria-label="Professional membership badge"></div>
  </footer>

  <div class="bottom-bar abs">
    <div class="copyright">Copyrights 2013. All Rights Reserved.</div>
    <div class="social"><span></span><span></span><span></span><span></span></div>
  </div>

</div>
</body>
</html>
```